New Year's card HTML

can you produce a best new years wishes 2018 design in HTML for our website as what I would like to send by email towards my network of candidates / customers ...

It must be wow, inspiring , design, meaningfull... MMM those people care about me, or those people will help me to go the extra mile, to help me to achieve my career goals, Your best move, enhance my possibilities, bring the love back

Target Market(s)

CEo's / CMO's/ HRDirectors network of 450k

Coding

Coded - Design and coding required

Number of Pages Required

1 page

Colors

Designer to choose colors to be used in the design.

Requirements
Must have
• Logo / visual / website adress www.moravintel.com and a call to action
Should not have
• no sound as our business is confidential

```html
<!DOCTYPE html>
<html lang="en">
<head>
<meta charset="utf-8">
<title>Moravintel – Happy New Year 2018</title>
<link rel="stylesheet" href="https://fonts.googleapis.com/css2?family=Cinzel:wght@500&family=Lato:wght@700;900&family=Fredoka+One&display=swap">
<style>
  :root {
    --navy-deep: #0c2049;
    --navy-mid: #1a3b74;
    --blue-glow: #3a6cb0;
    --gold: #f7c21b;
    --gold-dark: #c98a06;
    --gold-shadow: #8a5a02;
    --white: #ffffff;
    --soft-white: #dce6f5;
    --button-text: #14336b;
    --chart: rgba(120, 165, 225, 0.16);
    --arrow: rgba(150, 185, 235, 0.35);
  }
  * { margin: 0; padding: 0; box-sizing: border-box; }
  html, body { width: 1200px; height: 900px; overflow: hidden; background: var(--navy-deep); }
  .card {
    position: relative;
    width: 1200px;
    height: 900px;
    overflow: hidden;
    background:
      radial-gradient(ellipse 620px 480px at 600px 420px, var(--blue-glow) 0%, var(--navy-mid) 55%, var(--navy-deep) 100%);
    font-family: "Lato", Arial, sans-serif;
  }
  .chart-backdrop { position: absolute; inset: 0; }
  .sky-lights {
    position: absolute;
    left: 300px; top: 0; width: 700px; height: 200px;
    background: radial-gradient(ellipse 330px 110px at 50% 30%, rgba(255, 235, 180, 0.45), rgba(255, 210, 120, 0.12) 55%, transparent 80%);
  }
  .snowflake {
    position: absolute;
    border-radius: 50%;
    background: radial-gradient(circle, rgba(235, 242, 255, 0.55) 0%, rgba(210, 225, 250, 0.25) 50%, transparent 72%);
  }
  .brand {
    position: absolute;
    top: 200px; left: 0; width: 100%;
    display: flex; justify-content: center; align-items: center; gap: 16px;
  }
  .brand-dot { width: 18px; height: 18px; border-radius: 50%; background: var(--white); }
  .brand-name {
    font-family: "Cinzel", Georgia, serif;
    font-weight: 500;
    font-size: 58px;
    letter-spacing: 2px;
    color: var(--white);
    line-height: 1;
  }
  .greeting {
    position: absolute;
    top: 292px; left: 0; width: 100%;
    text-align: center;
    font-weight: 700;
    font-size: 38px;
    letter-spacing: 1px;
    color: var(--gold);
  }
  .year {
    position: absolute;
    top: 318px; left: 0; width: 100%;
    text-align: center;
    font-family: "Fredoka One", "Lato", sans-serif;
    font-weight: 400;
    font-size: 200px;
    line-height: 1;
    letter-spacing: 6px;
    color: var(--gold);
    text-shadow:
      0 2px 0 var(--gold-dark),
      0 4px 0 var(--gold-dark),
      0 6px 0 var(--gold-dark),
      0 8px 0 var(--gold-shadow),
      0 18px 22px rgba(0, 0, 0, 0.45);
  }
  .cta {
    position: absolute;
    left: 444px; top: 534px;
    width: 314px; height: 82px;
    border-radius: 41px;
    background: var(--white);
    border: 3px solid #cfdcf0;
    display: flex; align-items: center; justify-content: center;
    font-weight: 900;
    font-size: 26px;
    letter-spacing: 0.5px;
    color: var(--button-text);
    text-decoration: none;
  }
  .web-address {
    position: absolute;
    top: 626px; left: 0; width: 100%;
    text-align: center;
    font-weight: 700;
    font-size: 20px;
    letter-spacing: 1px;
    color: var(--soft-white);
  }
  .workspace-scene {
    position: absolute;
    left: 130px; top: 660px; width: 1040px; height: 240px;
    background: radial-gradient(ellipse 520px 200px at 50% 100%, rgba(200, 215, 240, 0.28), rgba(120, 150, 200, 0.12) 60%, transparent 85%);
  }
  .multiplier {
    position: absolute;
    right: 8px; bottom: 14px;
    font-weight: 900;
    font-size: 24px;
    color: var(--white);
  }
</style>
</head>
<body>
<main class="card">
  <svg class="chart-backdrop" width="1200" height="900" viewBox="0 0 1200 900" aria-hidden="true">
    <g fill="var(--chart)">
      <rect x="40" y="520" width="60" height="380"/>
      <rect x="120" y="440" width="60" height="460"/>
      <rect x="200" y="480" width="60" height="420"/>
      <rect x="280" y="400" width="60" height="500"/>
      <rect x="860" y="420" width="60" height="480"/>
      <rect x="940" y="360" width="60" height="540"/>
      <rect x="1020" y="460" width="60" height="440"/>
      <rect x="1100" y="380" width="60" height="520"/>
    </g>
    <g fill="none" stroke="var(--arrow)" stroke-width="14" stroke-linejoin="round" stroke-linecap="round">
      <polyline points="92,360 130,470 180,430 240,560 290,520 350,680"/>
      <polyline points="840,700 900,560 960,620 1030,460 1080,400 1135,315"/>
    </g>
    <g fill="var(--arrow)">
      <polygon points="84,312 114,362 66,372"/>
      <polygon points="1160,270 1152,332 1112,306"/>
    </g>
  </svg>

  <div class="sky-lights" role="img" aria-label="Fireworks burst and a string of glowing lights across the top"></div>
  <div class="snowflake" style="left:-30px;top:-30px;width:220px;height:220px" role="img" aria-label="Large white snowflake"></div>
  <div class="snowflake" style="left:150px;top:110px;width:150px;height:150px" role="img" aria-label="White snowflake"></div>
  <div class="snowflake" style="left:820px;top:-40px;width:150px;height:150px" role="img" aria-label="White snowflake"></div>
  <div class="snowflake" style="left:1040px;top:20px;width:200px;height:200px" role="img" aria-label="Large white snowflake"></div>
  <div class="snowflake" style="left:870px;top:220px;width:50px;height:50px" role="img" aria-label="Small white snowflake"></div>

  <div class="brand">
    <span class="brand-dot"></span>
    <span class="brand-name">MORAVINTEL</span>
  </div>

  <p class="greeting">HAPPY NEW YEAR</p>
  <h1 class="year">2018</h1>

  <a class="cta" href="https://www.moravintel.com">VISIT WEBSITE</a>
  <p class="web-address">www.moravintel.com</p>

  <div class="workspace-scene" role="img" aria-label="Illustrated hands holding a phone, a coin, a laptop, a megaphone, a calculator and a report"></div>
  <span class="multiplier">X10</span>
</main>
</body>
</html>
```